Website redesign www.marigoldlawpc.com law firm site

Need to redesign the website that I currently have to look more modern and professional. Would also like to be able to make updates and post without having a huge hassle. See current www.marigoldlawpc.com. I just think that it looks very immature and it's very templated there's no ability for me to make posts or Add links or anything like that

Target Market(s)

California people looking for a powerhouse attorney in

Industry/Entity Type

Legal

Number of Pages Required

3 page

Font styles to use
Serif
Sans Serif

Colors
ec1f27
000000
ffffff

Requirements
Must have
• Must be mobile friendly. Must look professional and have ability to post links to other websites. Must have ability to post blogs or articles. Would like to be able to read my FeeTrove account and also have the ability to upload forms for people to download
Nice to have
• Simple design easy to use and not cluttered with too much text

```html
<!DOCTYPE html>
<html lang="en">
<head>
<meta charset="utf-8">
<title>Marigold Law P.C.</title>
<link rel="stylesheet" href="https://fonts.googleapis.com/css2?family=Cinzel:wght@400;700&family=Roboto+Slab:wght@400&family=Roboto:wght@400;500;700&display=swap">
<style>
:root{
  --red:#ec1f27;
  --red-dark:#b5121a;
  --red-deep:#8e0c12;
  --black:#000000;
  --ink:#222222;
  --grey:#555555;
  --footer:#2b2b2b;
  --footer-bottom:#1c1c1c;
  --white:#ffffff;
  --line:#dddddd;
}
*{margin:0;padding:0;box-sizing:border-box}
html,body{width:1200px;height:3644px;overflow:hidden}
body{background:var(--white);font-family:"Roboto",Arial,sans-serif;color:var(--ink)}
section,header,nav,footer{position:relative;width:1200px}
.abs{position:absolute}
.center{left:0;right:0;text-align:center}
.slab{font-family:"Roboto Slab",Georgia,serif;font-weight:400}
.hl{color:var(--red)}

/* header */
.site-header{height:114px}
.brand{left:126px;top:26px;font-family:"Cinzel",Georgia,serif;font-size:40px;color:var(--red);font-weight:400;letter-spacing:1px}
.top-contact{top:38px;display:flex;align-items:center;gap:12px;font-size:16px;color:var(--ink)}
.top-contact .dot{width:34px;height:34px;border-radius:50%;background:var(--red);display:flex;align-items:center;justify-content:center}
.tc-phone{left:654px}
.tc-mail{left:842px}

/* nav */
.main-nav{height:44px}
.main-nav ul{position:absolute;left:66px;width:1068px;height:44px;background:var(--black);list-style:none;display:flex}
.main-nav li{font-family:"Cinzel",Georgia,serif;font-size:15px;color:var(--white);display:flex;align-items:center;justify-content:center;height:44px;flex:1}
.main-nav li.active{background:var(--red);flex:0 0 128px}

/* hero */
.hero{height:515px}
.hero-photo{position:absolute;inset:0;background:linear-gradient(120deg,#d9d9d9 0%,#8b8b8b 35%,#c97a3c 55%,#ececec 80%,#a8a8a8 100%)}
.hero-arrow{top:240px;width:30px;height:34px;background:rgba(0,0,0,.85);display:flex;align-items:center;justify-content:center}
.hero-caption{left:0;right:0;bottom:0;height:80px;background:rgba(20,20,20,.78);color:var(--white);font-family:"Cinzel",Georgia,serif;font-size:22px;line-height:30px;text-align:center;padding-top:10px;letter-spacing:.5px}

/* welcome */
.welcome{height:554px}
.section-title{font-size:33px;color:var(--ink)}
.welcome .section-title{top:40px}
.welcome-text{left:105px;width:990px;top:104px;font-size:14px;line-height:24px;color:var(--grey);text-align:center}
.btn-dark{top:202px;left:532px;width:136px;height:34px;background:#333;color:var(--white);font-size:15px;display:flex;align-items:center;justify-content:center}
.pillars{top:298px;left:140px;width:920px;display:flex;justify-content:space-between}
.pillar{width:260px;text-align:center}
.pillar h3{font-family:"Roboto Slab",Georgia,serif;font-weight:400;font-size:25px;color:var(--ink)}
.pillar .icon{width:86px;height:86px;margin:22px auto 18px;border-radius:50%;background:var(--red);display:flex;align-items:center;justify-content:center}
.pillar p{font-size:13px;line-height:19px;color:var(--grey)}

/* practice */
.practice{height:554px;background:linear-gradient(135deg,var(--red) 0%,var(--red-dark) 45%,#d41820 70%,var(--red-deep) 100%);color:var(--white)}
.practice .section-title{top:44px;color:var(--white)}
.practice-rule{top:100px;left:270px;width:660px;height:1px;background:rgba(255,255,255,.25)}
.arc{left:0;top:0}
.area{width:200px;font-size:12px;line-height:16px}
.area h4{font-family:"Roboto",Arial,sans-serif;font-weight:700;font-size:17px;line-height:22px}
.area.r{text-align:right}
.practice-brand{top:404px;font-family:"Cinzel",Georgia,serif;font-size:40px;color:var(--white)}

/* blog */
.blog{height:571px}
.blog .section-title{top:62px}
.post{top:163px;width:472px}
.post .date{position:absolute;left:0;top:0;width:44px;height:44px;background:var(--red);color:var(--white);text-align:center;font-size:14px;line-height:18px;padding-top:4px}
.post .date sup{font-size:9px}
.post h5{position:absolute;left:60px;top:0;width:410px;font-weight:400;font-size:16px;line-height:22px;color:var(--ink)}
.post .thumb{position:absolute;left:0;top:68px;width:472px;height:170px}
.post p{position:absolute;left:0;top:247px;width:472px;font-size:13px;line-height:19px;color:var(--grey)}
.dots{top:503px;display:flex;justify-content:center;gap:8px}
.dots i{width:8px;height:8px;border-radius:50%;background:#ccc;display:block}
.dots i.on{background:var(--red)}

/* testimonials */
.testimonials{height:386px;background:linear-gradient(135deg,var(--red-dark) 0%,var(--red) 40%,var(--red-dark) 75%,var(--red-deep) 100%);color:var(--white)}
.testimonials .section-title{top:38px;color:var(--white)}
.t-arrow{top:184px;width:34px;height:34px;border-radius:50%;background:#222;display:flex;align-items:center;justify-content:center}
.quote{top:114px;width:320px}
.quote .avatar{width:120px;height:120px;border-radius:50%;border:4px solid var(--white);margin:0 auto;background:radial-gradient(circle at 50% 40%,#d8c2a8 0%,#9aa3ad 60%,#e9e9e9 100%)}
.quote .mark{position:absolute;left:4px;top:140px;font-family:Georgia,serif;font-size:90px;line-height:90px;color:rgba(0,0,0,.25)}
.quote p{margin:14px 0 0 70px;width:240px;font-size:12px;line-height:16px;font-style:italic;text-align:center}
.quote .who{margin-top:14px;text-align:center;font-weight:700;font-size:14px}

/* ratings */
.ratings{height:396px}
.ratings .section-title{top:50px}
.ratings-sub{top:128px;font-size:12px;color:var(--grey)}
.badge-box{top:195px;width:276px;height:112px;border:1px solid var(--line);display:flex;align-items:center;justify-content:center}

/* newsletter */
.newsletter{height:146px;background:var(--red);color:var(--white)}
.nl-icon{left:100px;top:48px}
.nl-title{left:187px;top:38px;font-family:"Roboto Slab",Georgia,serif;font-size:27px}
.nl-sub{left:187px;top:78px;width:340px;font-size:11px;line-height:15px;color:#ffd3d5}
.nl-input{left:593px;top:52px;width:369px;height:42px;border:1px solid rgba(255,255,255,.8);font-size:12px;padding:13px 14px;color:#ffe2e3}
.nl-btn{left:982px;top:52px;width:121px;height:42px;background:var(--black);font-size:12px;font-weight:700;display:flex;align-items:center;justify-content:center;letter-spacing:.5px}

/* footer */
.site-footer{height:321px;background:var(--footer);color:#d8d8d8}
.f-col h6{font-family:"Roboto Slab",Georgia,serif;font-weight:400;font-size:19px;color:var(--white);padding-bottom:8px;border-bottom:1px solid #444;width:190px}
.f-col ul{list-style:none;margin-top:14px}
.f-col li{font-size:13px;line-height:31px}
.f-col li::before{content:"› ";color:var(--red)}
.f-col li.on{color:var(--red)}
.f-contact p{font-size:13px;line-height:19px;margin-top:14px}
.f-contact .row{display:flex;align-items:center;gap:8px;margin-top:16px;font-size:13px}
.map{left:554px;top:86px;width:256px;height:165px;background:linear-gradient(160deg,#eef0ea 0%,#dfe4da 60%,#cfd8e4 100%)}
.pay{left:850px;top:98px;width:241px;height:133px;background:var(--white);border:1px solid #999;text-align:center;color:#1f3b6e}
.pay small{display:block;margin-top:10px;font-size:11px;font-weight:700}
.pay strong{display:block;margin-top:18px;font-family:"Roboto",Arial,sans-serif;font-weight:700;font-size:38px;color:#1f3b6e}
.bottom-bar{height:43px;background:var(--footer-bottom);color:#bbb;font-size:12px}
.bottom-bar .copy{left:100px;top:14px}
.social{right:100px;top:10px;display:flex;gap:8px}
.social i{display:block;width:22px;height:22px;border-radius:50%}
</style>
</head>
<body>

<header class="site-header">
  <div class="abs brand">Marigold Law P.C.</div>
  <div class="abs top-contact tc-phone">
    <span class="dot"><svg width="16" height="16" viewBox="0 0 24 24"><path fill="#fff" d="M6.6 10.8a15.1 15.1 0 0 0 6.6 6.6l2.2-2.2c.3-.3.7-.4 1-.2 1.1.4 2.3.6 3.6.6.6 0 1 .4 1 1V20c0 .6-.4 1-1 1A17 17 0 0 1 3 4c0-.6.4-1 1-1h3.5c.6 0 1 .4 1 1 0 1.3.2 2.5.6 3.6.1.3 0 .7-.2 1z"/></svg></span>
    (530) 555-0148
  </div>
  <div class="abs top-contact tc-mail">
    <span class="dot"><svg width="16" height="16" viewBox="0 0 24 24"><path fill="#fff" d="M3 5h18v14H3z"/><path fill="none" stroke="#ec1f27" stroke-width="2" d="M3 6l9 7 9-7"/></svg></span>
    dana@marigoldlawgroup.com
  </div>
</header>

<nav class="main-nav">
  <ul>
    <li class="active">Home</li>
    <li>Attorney Profile</li>
    <li>Practice Areas &#9662;</li>
    <li>Client Reviews</li>
    <li>Links</li>
    <li>Contact Us</li>
  </ul>
</nav>

<section class="hero">
  <div class="hero-photo" role="img" aria-label="Attorney at a desk signing a document beside a small model house"></div>
  <div class="abs hero-arrow" style="left:0"><svg width="10" height="14" viewBox="0 0 10 14"><path d="M8 1L2 7l6 6" stroke="#fff" stroke-width="2.5" fill="none"/></svg></div>
  <div class="abs hero-arrow" style="right:0"><svg width="10" height="14" viewBox="0 0 10 14"><path d="M2 1l6 6-6 6" stroke="#fff" stroke-width="2.5" fill="none"/></svg></div>
  <div class="hero-caption abs">A Boutique Law Firm Opportunity For Clients Who Want To Enjoy All The<br>Advantages Of Dana's Broad Legal Experience And Education.</div>
</section>

<section class="welcome">
  <h2 class="abs center section-title slab">Welcome to <span class="hl">Marigold Law P.C</span></h2>
  <p class="abs welcome-text">Marigold Law P.C. is owned by Dana L. Hollis, a dedicated and caring professional who uses her broad range of skills as a California lawyer to bring consumers and business owners exceptionally strong legal representation that achieves best results. She works with people from across the northern region of California, from the Northern border to the Central Valley region.</p>
  <div class="abs btn-dark">Read More</div>
  <div class="abs pillars">
    <div class="pillar">
      <h3>Mission</h3>
      <div class="icon"><svg width="46" height="46" viewBox="0 0 46 46"><circle cx="23" cy="23" r="17" fill="none" stroke="#fff" stroke-width="4"/><circle cx="23" cy="23" r="9" fill="none" stroke="#fff" stroke-width="4"/><circle cx="23" cy="23" r="3" fill="#fff"/><path d="M23 23L40 6" stroke="#fff" stroke-width="3"/></svg></div>
      <p>Sed ut perspiciatis unde omnis iste natus error sit voluptatem accusantium doloremque laudantium,</p>
    </div>
    <div class="pillar">
      <h3>Vision</h3>
      <div class="icon"><svg width="50" height="30" viewBox="0 0 50 30"><path d="M2 15C10 3 40 3 48 15 40 27 10 27 2 15z" fill="#fff"/><circle cx="25" cy="15" r="8" fill="#ec1f27"/><circle cx="25" cy="15" r="3.5" fill="#fff"/></svg></div>
      <p>Sed ut perspiciatis unde omnis iste natus error sit voluptatem accusantium doloremque laudantium,</p>
    </div>
    <div class="pillar">
      <h3>Values</h3>
      <div class="icon"><svg width="44" height="40" viewBox="0 0 44 40"><rect x="4" y="24" width="7" height="14" fill="#fff"/><rect x="14" y="18" width="7" height="20" fill="#fff"/><rect x="24" y="12" width="7" height="26" fill="#fff"/><rect x="34" y="6" width="7" height="32" fill="#fff"/><path d="M4 16L20 6l8 4L40 2" stroke="#fff" stroke-width="2.5" fill="none"/></svg></div>
      <p>Sed ut perspiciatis unde omnis iste natus error sit voluptatem accusantium doloremque laudantium,</p>
    </div>
  </div>
</section>

<section class="practice">
  <h2 class="abs center section-title slab">Practice Areas</h2>
  <div class="abs practice-rule"></div>
  <svg class="abs arc" width="1200" height="554" viewBox="0 0 1200 554">
    <path d="M325 486 A275 275 0 0 1 875 486" fill="none" stroke="#fff" stroke-width="4"/>
    <g fill="#fff" stroke="#ec1f27" stroke-width="0">
      <circle cx="600" cy="211" r="30"/>
      <circle cx="438" cy="263" r="30"/>
      <circle cx="762" cy="263" r="30"/>
      <circle cx="351" cy="370" r="30"/>
      <circle cx="849" cy="370" r="30"/>
      <circle cx="325" cy="476" r="30"/>
      <circle cx="875" cy="476" r="30"/>
    </g>
    <g fill="#ec1f27">
      <circle cx="590" cy="204" r="5"/><circle cx="610" cy="204" r="5"/><circle cx="600" cy="214" r="5"/>
      <rect x="587" y="212" width="26" height="10" rx="4"/>
      <circle cx="438" cy="263" r="14"/>
      <circle cx="756" cy="263" r="9" fill="none" stroke="#ec1f27" stroke-width="4"/><circle cx="770" cy="263" r="9" fill="none" stroke="#ec1f27" stroke-width="4"/>
      <path d="M336 372l15-14 15 14h-5v12h-20v-12z"/>
      <path d="M834 378a15 15 0 0 1 30 0z"/><rect x="832" y="378" width="34" height="5"/>
      <rect x="311" y="468" width="28" height="20" rx="3"/><rect x="319" y="462" width="12" height="7" fill="none" stroke="#ec1f27" stroke-width="3"/>
      <rect x="865" y="466" width="20" height="20" rx="2"/>
    </g>
    <path d="M434 255h8M432 263h12M434 271h8" stroke="#fff" stroke-width="2.5"/>
    <path d="M870 470l10 10M880 470l-10 10" stroke="#fff" stroke-width="2.5"/>
  </svg>
  <div class="abs area" style="left:500px;top:118px;text-align:center"><h4>Family Law</h4>Sed ut perspiciatis unde omnis<br>sit voluptatem accusantium</div>
  <div class="abs area r" style="left:198px;top:212px"><h4>Bankruptcy</h4>Sed ut perspiciatis unde omnis<br>sit voluptatem accusantium</div>
  <div class="abs area" style="left:809px;top:212px"><h4>Criminal Law</h4>Sed ut perspiciatis unde omnis<br>sit voluptatem accusantium</div>
  <div class="abs area r" style="left:111px;top:322px"><h4>Real Estate Law</h4>Sed ut perspiciatis unde omnis<br>sit voluptatem accusantium</div>
  <div class="abs area" style="left:885px;top:322px"><h4>Civil Litigation</h4>Sed ut perspiciatis unde omnis<br>sit voluptatem accusantium</div>
  <div class="abs area r" style="left:84px;top:452px"><h4>Business Law</h4>Sed ut perspiciatis unde omnis<br>sit voluptatem accusantium</div>
  <div class="abs area" style="left:926px;top:452px"><h4>Unlawful Detainer</h4>Sed ut perspiciatis unde omnis<br>sit voluptatem accusantium</div>
  <div class="abs center practice-brand">Marigold Law P.C.</div>
</section>

<section class="blog">
  <h2 class="abs center section-title slab">Latest From <span class="hl">Our Blog</span></h2>
  <article class="abs post" style="left:102px">
    <div class="date">17<sup>th</sup><br>Feb</div>
    <h5>Lorem ipsum dolor sit amet, consectetuer adipiscing elit doloremque.</h5>
    <div class="thumb" role="img" aria-label="Judge's gavel resting on a historic constitution document" style="background:linear-gradient(100deg,#e6d3a8 0%,#c7a66b 45%,#5a3a1e 70%,#2c1a0d 100%)"></div>
    <p>Fusce elementum, nulla vel pellentes consequat, ante nulla hendrerit arcu, ac tincidunt mauris lacus sed leo. vamus suscipit molestie vestibulum. Lorem ipsum dolor sit amet,</p>
  </article>
  <article class="abs post" style="left:630px">
    <div class="date">17<sup>th</sup><br>Feb</div>
    <h5>Lorem ipsum dolor sit amet, consectetuer adipiscing elit doloremque.</h5>
    <div class="thumb" role="img" aria-label="Brass scales of justice in a wood-panelled courtroom" style="background:linear-gradient(100deg,#7a3a16 0%,#b5652a 40%,#d9a45a 60%,#6a3212 100%)"></div>
    <p>Fusce elementum, nulla vel pellentes consequat, ante nulla hendrerit arcu, ac tincidunt mauris lacus sed leo. vamus suscipit molestie vestibulum. Lorem ipsum dolor sit amet,</p>
  </article>
  <div class="abs center dots"><i class="on"></i><i></i><i></i><i></i></div>
</section>

<section class="testimonials">
  <h2 class="abs center section-title slab">What Peoples Say</h2>
  <div class="abs t-arrow" style="left:62px"><svg width="10" height="14" viewBox="0 0 10 14"><path d="M8 1L2 7l6 6" stroke="#fff" stroke-width="2.5" fill="none"/></svg></div>
  <div class="abs t-arrow" style="left:1104px"><svg width="10" height="14" viewBox="0 0 10 14"><path d="M2 1l6 6-6 6" stroke="#fff" stroke-width="2.5" fill="none"/></svg></div>
  <div class="abs quote" style="left:107px">
    <div class="avatar" role="img" aria-label="Portrait photo of a client"></div>
    <span class="mark">&ldquo;</span>
    <p>Lorem ipsum dolor sit amet, consectetuer adipiscing elit, sed diam nonummy Lorem ipsum dolor sit amet, consectetuer adipiscing elit,</p>
    <div class="who">- Consectetue Radipiscing</div>
  </div>
  <div class="abs quote" style="left:440px">
    <div class="avatar" role="img" aria-label="Portrait photo of a client"></div>
    <span class="mark">&ldquo;</span>
    <p>Lorem ipsum dolor sit amet, consectetuer adipiscing elit, sed diam nonummy Lorem ipsum dolor sit amet, consectetuer adipiscing elit,</p>
    <div class="who">- Diam Nonummy</div>
  </div>
  <div class="abs quote" style="left:778px">
    <div class="avatar" role="img" aria-label="Portrait photo of a client"></div>
    <span class="mark">&ldquo;</span>
    <p>Lorem ipsum dolor sit amet, consectetuer adipiscing elit, sed diam nonummy Lorem ipsum dolor sit amet, consectetuer adipiscing elit,</p>
    <div class="who">- Dolor Sitamet</div>
  </div>
</section>

<section class="ratings">
  <h2 class="abs center section-title slab">Ratings and <span class="hl">Reviews</span></h2>
  <p class="abs center ratings-sub">Lawyer Dana L. Hollis, Esq. &nbsp;&nbsp;|&nbsp;&nbsp; Featured Attorney Bankruptcy / Chapter 7</p>
  <div class="abs badge-box" style="left:138px"><svg width="80" height="80"><circle cx="40" cy="40" r="36" fill="#1f4e8c"/></svg></div>
  <div class="abs badge-box" style="left:462px"><svg width="80" height="80"><circle cx="40" cy="40" r="36" fill="none" stroke="#555" stroke-width="3"/></svg></div>
  <div class="abs badge-box" style="left:786px"><svg width="180" height="40"><rect x="0" y="6" width="180" height="28" fill="#5a6f8f"/></svg></div>
</section>

<section class="newsletter">
  <svg class="abs nl-icon" width="64" height="48" viewBox="0 0 64 48"><rect x="2" y="2" width="60" height="44" fill="none" stroke="#fff" stroke-width="3"/><path d="M2 2l30 24L62 2M2 46l22-22M62 46L40 24" fill="none" stroke="#fff" stroke-width="3"/></svg>
  <div class="abs nl-title">Subscribe To Our Newsletter</div>
  <div class="abs nl-sub">Aenean tortor adipiscing elit, sed diam nonummy nibh euismod tin cidunt ut volutpat velit esse molestie...</div>
  <div class="abs nl-input">Enter Your Email Here</div>
  <div class="abs nl-btn">SUBSCRIBE</div>
</section>

<footer class="site-footer">
  <div class="abs f-col" style="left:100px;top:48px">
    <h6>Quick <span class="hl">Links</span></h6>
    <ul>
      <li class="on">Home</li><li>Attorney Profile</li><li>Practice Areas</li><li>Client Reviews</li><li>Links</li><li>Blog</li><li>Contact Us</li>
    </ul>
  </div>
  <div class="abs f-col f-contact" style="left:301px;top:48px">
    <h6>Contact <span class="hl">Details</span></h6>
    <p>Marigold Law P.C<br>410 Orchard Lane<br>Suite 200, Redding, CA 96001</p>
    <div class="row"><svg width="14" height="14" viewBox="0 0 24 24"><path fill="#ddd" d="M6.6 10.8a15.1 15.1 0 0 0 6.6 6.6l2.2-2.2c.3-.3.7-.4 1-.2 1.1.4 2.3.6 3.6.6.6 0 1 .4 1 1V20c0 .6-.4 1-1 1A17 17 0 0 1 3 4c0-.6.4-1 1-1h3.5c.6 0 1 .4 1 1 0 1.3.2 2.5.6 3.6.1.3 0 .7-.2 1z"/></svg>(530) 555-0148</div>
    <div class="row"><svg width="14" height="14" viewBox="0 0 24 24"><rect x="4" y="2" width="16" height="20" rx="2" fill="none" stroke="#ddd" stroke-width="2"/></svg>(888) 555-0193</div>
    <div class="row"><svg width="14" height="14" viewBox="0 0 24 24"><path fill="#ddd" d="M2 5h20v14H2z"/><path d="M2 6l10 7 10-7" stroke="#2b2b2b" stroke-width="2" fill="none"/></svg>dana@marigoldlawgroup.com</div>
  </div>
  <div class="abs f-col" style="left:554px;top:48px"><h6>Location <span class="hl">Map</span></h6></div>
  <div class="abs map" role="img" aria-label="Street map showing the office location"></div>
  <div class="abs pay">
    <small>Make Secure Online Payment</small>
    <strong>FeeTrove</strong>
  </div>
</footer>

<div class="bottom-bar" style="position:relative;width:1200px">
  <div class="abs copy">&copy; 2016 Marigold Law P.C . All Rights Reserved.</div>
  <div class="abs social"><i style="background:#3b5998"></i><i style="background:#0e76a8"></i><i style="background:#2aa4e6"></i></div>
</div>

</body>
</html>
```